Stained Glass Wedding Invitation/Stationary Design

Hello! We need a wedding invitation/stationary/design that incorporates vibrant stained glass of the type found in the Tornavela Olmeda (see images attached for reference), combined with art deco lettering. We are looking for 1) Invitation design 2) resuable fonts/graphic elements that be used for menus, signs, etc.
Other font styles liked:
- Anything art deco

Colors
ec1f27
6b449b
0293ce
9bcb3c
ffc214
Requirements
Must have
- Vibrant modern stained glass (as per styles in attached photos) as an accent, art deco design for fonts etc.

Nice to have
- designs representing travel/wine

Should not have
- formal/traditional stained glass look

```html
<!DOCTYPE html>
<html lang="en">
<head>
<meta charset="utf-8">
<title>Stained Glass Wedding Invitation – Six Samples</title>
<link rel="stylesheet" href="https://fonts.googleapis.com/css2?family=Cinzel:wght@400;700&family=Limelight&family=Great+Vibes&family=Parisienne&family=Marcellus&display=swap">
<style>
  :root {
    --board: #2b2b2b;
    --label: #f2f2f2;
    --navy: #141a33;
    --deep-teal: #0c2528;
    --paper: #ffffff;
    --orange: #f7931e;
    --tan: #c38a52;
    --rust: #c0390f;
    --ink: #2a2a2a;
    --ink-soft: #444444;
    --navy-ink: #1f4f8c;
    --teal: #18a5c2;
    --light-ink: #e8e8e8;
    --red: #ec1f27;
    --purple: #6b449b;
    --blue: #0293ce;
    --green: #9bcb3c;
    --yellow: #ffc214;
  }
  * { box-sizing: border-box; margin: 0; padding: 0; }
  html, body { width: 1196px; height: 1200px; overflow: hidden; background: var(--board); }
  .board { position: relative; width: 1196px; height: 1200px; }

  .sample-label {
    position: absolute;
    font-family: "Cinzel", serif;
    font-weight: 700;
    font-size: 11px;
    letter-spacing: 0.5px;
    color: var(--label);
  }

  .card {
    position: absolute;
    width: 313px;
    height: 443px;
    overflow: hidden;
    box-shadow: 0 4px 10px rgba(0,0,0,0.35);
  }
  .card--navy { background: var(--navy); }
  .card--teal { background: var(--deep-teal); }
  .card--white { background: var(--paper); }

  .art { position: absolute; }
  .frame { position: absolute; left: 0; top: 0; }

  .copy {
    position: absolute;
    left: 0;
    width: 313px;
    text-align: center;
  }
  .copy p { display: block; }
  .together {
    font-family: "Cinzel", serif;
    font-size: 8px;
    line-height: 10px;
    letter-spacing: 0.2px;
  }
  .name {
    font-family: "Limelight", "Poiret One", serif;
    font-size: 46px;
    line-height: 48px;
  }
  .name--first { margin-top: 18px; }
  .name--script {
    font-family: "Great Vibes", cursive;
    font-size: 64px;
    line-height: 60px;
  }
  .amp {
    font-family: "Parisienne", cursive;
    font-size: 24px;
    line-height: 20px;
  }
  .invite {
    margin-top: 14px;
    font-family: "Cinzel", serif;
    font-size: 8.5px;
    line-height: 13px;
    letter-spacing: 0.3px;
  }
  .when {
    margin-top: 10px;
    font-family: "Marcellus", serif;
    font-size: 19px;
    line-height: 26px;
    letter-spacing: 0.5px;
  }
  .address {
    margin-top: 12px;
    font-family: "Cinzel", serif;
    font-size: 5.5px;
    line-height: 9px;
  }
  .reception {
    margin-top: 12px;
    font-family: "Parisienne", cursive;
    font-size: 9px;
    line-height: 12px;
  }

  /* colour themes */
  .theme-light .together, .theme-light .invite, .theme-light .address { color: var(--ink); }
  .theme-light .amp, .theme-light .reception { color: var(--ink); }
  .theme-light .name { color: var(--orange); }
  .theme-light .when { color: var(--ink); }
  .theme-light.when-navy .when { color: var(--navy-ink); }

  .theme-dark .together, .theme-dark .invite, .theme-dark .address { color: var(--light-ink); }
  .theme-dark .amp { color: var(--paper); }
  .theme-dark .when { color: var(--teal); }
  .theme-dark .reception { color: var(--orange); }
  .theme-dark .name { color: var(--tan); }
  .theme-dark.reception-teal .reception { color: var(--teal); }
  .name--orange { color: var(--orange) !important; }
  .name--rust { color: var(--rust) !important; }
</style>
</head>
<body>
<main class="board">

  <span class="sample-label" style="left:61px; top:92px;">SAMPLE 1</span>
  <span class="sample-label" style="left:438px; top:92px;">SAMPLE 2</span>
  <span class="sample-label" style="left:815px; top:92px;">SAMPLE 3</span>
  <span class="sample-label" style="left:61px; top:1107px;">SAMPLE 4</span>
  <span class="sample-label" style="left:438px; top:1107px;">SAMPLE 5</span>
  <span class="sample-label" style="left:815px; top:1107px;">SAMPLE 6</span>

  <!-- Sample 1: navy, stained-glass foliage wreath -->
  <section class="card card--navy" style="left:62px; top:125px;">
    <div class="art" role="img" aria-label="Stained glass autumn foliage wreath around the frame"
         style="left:14px; top:22px; width:290px; height:400px; border-radius:40px;
         background: linear-gradient(180deg, #e8631b 0%, #f2a12a 25%, #2a6fb0 55%, #d9541a 85%, #f08a22 100%); opacity:0.9;"></div>
    <svg class="frame" width="313" height="443" viewBox="0 0 313 443" aria-hidden="true">
      <defs>
        <linearGradient id="glass1" x1="0" y1="0" x2="1" y2="1">
          <stop offset="0" stop-color="#ec1f27"/><stop offset="0.3" stop-color="#ffc214"/>
          <stop offset="0.55" stop-color="#0293ce"/><stop offset="0.8" stop-color="#9bcb3c"/>
          <stop offset="1" stop-color="#ec1f27"/>
        </linearGradient>
      </defs>
      <path d="M 61 62 H 254 A 14 14 0 0 0 268 76 V 372 A 14 14 0 0 0 254 386 H 61 A 14 14 0 0 0 47 372 V 76 A 14 14 0 0 0 61 62 Z" fill="#ffffff" stroke="url(#glass1)" stroke-width="5"/>
      <path d="M 63 66 H 252 A 12 12 0 0 0 264 78 V 370 A 12 12 0 0 0 252 382 H 63 A 12 12 0 0 0 51 370 V 78 A 12 12 0 0 0 63 66 Z" fill="none" stroke="#5a3a1e" stroke-width="0.8"/>
    </svg>
    <div class="copy theme-light when-navy" style="top:96px;">
      <p class="together">TOGETHER WITH THEIR FAMILIES</p>
      <p class="name name--first" style="font-size:40px;">Bride</p>
      <p class="amp">and</p>
      <p class="name" style="font-size:40px;">Groom</p>
      <p class="invite">INVITE YOU TO JOIN THEM<br>AT THEIR WEDDING</p>
      <p class="when" style="font-size:17px;">DAY | DATE | YEAR</p>
      <p class="address">ADDRESS : LOREM IPSUM DUMMY TEXT<br>LOREM IPSUM DUMMY TEXT</p>
      <p class="reception">Reception to</p>
    </div>
  </section>

  <!-- Sample 2: white, watercolour greenery corners -->
  <section class="card card--white" style="left:438px; top:125px;">
    <div class="art" role="img" aria-label="Watercolour greenery leaves along the top edge"
         style="left:0; top:0; width:230px; height:45px; background: linear-gradient(90deg, #8aa58a, #b59a8a 60%, rgba(255,255,255,0));"></div>
    <div class="art" role="img" aria-label="Watercolour greenery leaves along the left edge"
         style="left:0; top:30px; width:32px; height:240px; background: linear-gradient(180deg, #9bb09a, #7d9670 60%, rgba(255,255,255,0));"></div>
    <div class="art" role="img" aria-label="Watercolour greenery leaves in the lower right corner"
         style="left:270px; top:210px; width:43px; height:233px; background: linear-gradient(180deg, rgba(255,255,255,0), #7fa36a 40%, #b59575);"></div>
    <div class="art" role="img" aria-label="Watercolour greenery leaves along the bottom edge"
         style="left:90px; top:405px; width:223px; height:38px; background: linear-gradient(90deg, rgba(255,255,255,0), #a89a84 30%, #8aa070);"></div>
    <svg class="frame" width="313" height="443" viewBox="0 0 313 443" aria-hidden="true">
      <defs>
        <linearGradient id="glass2" x1="0" y1="0" x2="1" y2="1">
          <stop offset="0" stop-color="#ec1f27"/><stop offset="0.3" stop-color="#0293ce"/>
          <stop offset="0.6" stop-color="#ffc214"/><stop offset="1" stop-color="#6b449b"/>
        </linearGradient>
      </defs>
      <path d="M 52 43 H 263 A 16 16 0 0 0 279 59 V 380 A 16 16 0 0 0 263 396 H 52 A 16 16 0 0 0 36 380 V 59 A 16 16 0 0 0 52 43 Z" fill="#ffffff" stroke="url(#glass2)" stroke-width="5"/>
      <path d="M 54 48 H 261 A 13 13 0 0 0 274 61 V 378 A 13 13 0 0 0 261 391 H 54 A 13 13 0 0 0 41 378 V 61 A 13 13 0 0 0 54 48 Z" fill="none" stroke="#5a3a1e" stroke-width="0.8"/>
    </svg>
    <div class="copy theme-light" style="top:84px;">
      <p class="together">TOGETHER WITH THEIR FAMILIES</p>
      <p class="name name--first">Bride</p>
      <p class="amp">and</p>
      <p class="name">Groom</p>
      <p class="invite">INVITE YOU TO JOIN THEM<br>AT THEIR WEDDING</p>
      <p class="when">DAY | DATE | YEAR</p>
      <p class="address">ADDRESS : LOREM IPSUM DUMMY TEXT<br>LOREM IPSUM DUMMY TEXT</p>
      <p class="reception">Reception to</p>
    </div>
  </section>

  <!-- Sample 3: navy, stained-glass ogee bands -->
  <section class="card card--navy" style="left:815px; top:125px;">
    <div class="art" role="img" aria-label="Stained glass ogee pattern band"
         style="left:0; top:0; width:313px; height:73px; background: linear-gradient(90deg, #0293ce, #ffc214 25%, #ec1f27 45%, #ffc214 65%, #0293ce 85%, #9bcb3c);"></div>
    <div class="art" role="img" aria-label="Stained glass ogee pattern band"
         style="left:0; top:402px; width:313px; height:41px; background: linear-gradient(90deg, #9bcb3c, #ffc214 30%, #0293ce 55%, #ffc214 80%, #ec1f27);"></div>
    <div class="copy theme-dark" style="top:94px;">
      <p class="together">TOGETHER WITH THEIR FAMILIES</p>
      <p class="name name--first">Bride</p>
      <p class="amp">and</p>
      <p class="name">Groom</p>
      <p class="invite">INVITE YOU TO JOIN THEM<br>AT THEIR WEDDING</p>
      <p class="when">DAY | DATE | YEAR</p>
      <p class="address">ADDRESS : LOREM IPSUM DUMMY TEXT<br>LOREM IPSUM DUMMY TEXT</p>
      <p class="reception">Reception to</p>
    </div>
  </section>

  <!-- Sample 4: deep teal, scallop band, script names -->
  <section class="card card--teal" style="left:62px; top:635px;">
    <svg class="frame" width="313" height="443" viewBox="0 0 313 443" aria-hidden="true">
      <defs>
        <linearGradient id="glass4" x1="0" y1="0" x2="1" y2="1">
          <stop offset="0" stop-color="#0293ce"/><stop offset="0.4" stop-color="#ffc214"/>
          <stop offset="0.7" stop-color="#ec1f27"/><stop offset="1" stop-color="#c38a52"/>
        </linearGradient>
      </defs>
      <path d="M 30 58 H 286 V 401 A 16 16 0 0 0 270 417 H 46 A 16 16 0 0 0 30 401 Z" fill="none" stroke="url(#glass4)" stroke-width="1.4"/>
    </svg>
    <div class="art" role="img" aria-label="Iridescent scallop pattern band"
         style="left:0; top:0; width:313px; height:61px; background: linear-gradient(90deg, #c38a52, #9bcb3c 25%, #0293ce 50%, #ffc214 75%, #c38a52);"></div>
    <div class="copy theme-dark" style="top:79px;">
      <p class="together">TOGETHER WITH THEIR FAMILIES</p>
      <p class="name name--script" style="margin-top:10px;">Bride</p>
      <p class="amp">and</p>
      <p class="name name--script">Groom</p>
      <p class="invite">INVITE YOU TO JOIN THEM<br>AT THEIR WEDDING</p>
      <p class="when">DAY | DATE | YEAR</p>
      <p class="address">ADDRESS : LOREM IPSUM DUMMY TEXT<br>LOREM IPSUM DUMMY TEXT</p>
      <p class="reception">Reception to</p>
    </div>
  </section>

  <!-- Sample 5: white, stained-glass mosaic and arched windows -->
  <section class="card card--white" style="left:438px; top:635px;">
    <div class="art" role="img" aria-label="Vibrant stained glass mosaic band"
         style="left:0; top:0; width:313px; height:117px; background: linear-gradient(90deg, #ec1f27, #ffc214 20%, #0293ce 40%, #ec1f27 60%, #ffc214 80%, #0293ce);"></div>
    <div class="art" role="img" aria-label="Stained glass arched windows, lower left"
         style="left:0; top:303px; width:100px; height:140px; background: linear-gradient(90deg, #ffc214, #ec1f27 45%, #9bcb3c);"></div>
    <div class="art" role="img" aria-label="Stained glass arched windows, lower right"
         style="left:213px; top:303px; width:100px; height:140px; background: linear-gradient(90deg, #ffc214, #ec1f27 45%, #9bcb3c);"></div>
    <svg class="frame" width="313" height="443" viewBox="0 0 313 443" aria-hidden="true">
      <defs>
        <linearGradient id="glass5" x1="0" y1="0" x2="1" y2="1">
          <stop offset="0" stop-color="#ec1f27"/><stop offset="0.35" stop-color="#0293ce"/>
          <stop offset="0.7" stop-color="#ffc214"/><stop offset="1" stop-color="#6b449b"/>
        </linearGradient>
      </defs>
      <path d="M 52 48 H 263 A 16 16 0 0 0 279 64 V 385 A 16 16 0 0 0 263 401 H 52 A 16 16 0 0 0 36 385 V 64 A 16 16 0 0 0 52 48 Z" fill="#ffffff" stroke="url(#glass5)" stroke-width="5"/>
      <path d="M 54 53 H 261 A 13 13 0 0 0 274 66 V 383 A 13 13 0 0 0 261 396 H 54 A 13 13 0 0 0 41 383 V 66 A 13 13 0 0 0 54 53 Z" fill="none" stroke="#5a3a1e" stroke-width="0.8"/>
    </svg>
    <div class="copy theme-light" style="top:85px;">
      <p class="together">TOGETHER WITH THEIR FAMILIES</p>
      <p class="name name--first">Bride</p>
      <p class="amp">and</p>
      <p class="name">Groom</p>
      <p class="invite">INVITE YOU TO JOIN THEM<br>AT THEIR WEDDING</p>
      <p class="when">DAY | DATE | YEAR</p>
      <p class="address">ADDRESS : LOREM IPSUM DUMMY TEXT<br>LOREM IPSUM DUMMY TEXT</p>
      <p class="reception">Reception to</p>
    </div>
  </section>

  <!-- Sample 6: navy, mosaic band and arched windows -->
  <section class="card card--navy" style="left:815px; top:635px;">
    <div class="art" role="img" aria-label="Vibrant stained glass mosaic band"
         style="left:0; top:0; width:313px; height:51px; background: linear-gradient(90deg, #ec1f27, #f08a22 30%, #0293ce 60%, #2a6fb0 80%, #ec1f27);"></div>
    <div class="art" role="img" aria-label="Stained glass arched windows, lower left"
         style="left:0; top:304px; width:100px; height:139px; background: linear-gradient(90deg, #ffc214, #ec1f27 45%, #9bcb3c);"></div>
    <div class="art" role="img" aria-label="Stained glass arched windows, lower right"
         style="left:215px; top:304px; width:98px; height:139px; background: linear-gradient(90deg, #ffc214, #ec1f27 45%, #9bcb3c);"></div>
    <div class="copy theme-dark reception-teal" style="top:71px;">
      <p class="together">TOGETHER WITH THEIR FAMILIES</p>
      <p class="name name--first name--orange">Bride</p>
      <p class="amp">and</p>
      <p class="name name--rust">Groom</p>
      <p class="invite">INVITE YOU TO JOIN THEM<br>AT THEIR WEDDING</p>
      <p class="when">DAY | DATE | YEAR</p>
      <p class="address">ADDRESS : LOREM IPSUM DUMMY TEXT<br>LOREM IPSUM DUMMY TEXT</p>
      <p class="reception">Reception to</p>
    </div>
  </section>

</main>
</body>
</html>
```